Silver Bloom Marisol's Cleaning Service Business Cards Project

A business card with all contact details with logo design on there (already have a logo) eye catching Logo and contact info on one side, full logo on the back, must target upper class residential and corporate companies, fitness companies, still keep it on the feminine side of things , must look elegant

Target Market(s)

Upper class homes and corporate companies

Industry/Entity Type

Cleaning Service

Contact Information for Business Card

Name: Marisol Quenby
Position: Director
ABN: 31647209853
Email: marisolssilvercleaning@tidymail.example
Number: 0417906354

Font styles to use
Decorative

Colors

Designer to choose colors to be used in the design.

Requirements
Must have
• Available Sydney Wide, contact info and logo on one side, full logo on the back
Nice to have
• Professional appearance
Should not have
• Cheap advert looking stuff

```html
<!DOCTYPE html>
<html lang="en">
<head>
<meta charset="utf-8">
<title>Silver Bloom – Business Cards</title>
<link rel="stylesheet" href="https://fonts.googleapis.com/css2?family=Lato:wght@400&family=Noticia+Text:wght@400;700&display=swap">
<style>
  :root {
    --backdrop: #8a4f2a;
    --kraft-light: #dcbb92;
    --kraft-mid: #cfa77a;
    --kraft-dark: #c3976a;
    --ink: #151311;
    --brand-ink: #2f3446;
    --ornament-tone: rgba(47, 52, 70, 0.28);
    --ornament-fade: rgba(47, 52, 70, 0);
    --card-shadow: rgba(0, 0, 0, 0.45);
  }
  * { margin: 0; padding: 0; box-sizing: border-box; }
  html, body {
    width: 1200px;
    height: 900px;
    overflow: hidden;
  }
  body {
    position: relative;
    background: var(--backdrop);
  }
  .card {
    position: absolute;
    width: 556px;
    height: 343px;
    background: radial-gradient(ellipse at 55% 20%, var(--kraft-light) 0%, var(--kraft-mid) 55%, var(--kraft-dark) 100%);
    box-shadow: 2px 4px 6px var(--card-shadow);
    text-align: center;
    color: var(--ink);
  }
  .card--front { left: 330px; top: 90px; }
  .card--back  { left: 330px; top: 469px; width: 559px; }

  .contact {
    position: absolute;
    left: 0; right: 0;
    top: 95px;
    font-family: "Lato", sans-serif;
    font-size: 15px;
    line-height: 21px;
  }
  .contact__name {
    font-family: "Noticia Text", serif;
    font-weight: 400;
    font-size: 22px;
    line-height: 24px;
    letter-spacing: 0.5px;
  }
  .contact__role { margin-bottom: 16px; }
  .contact__abn { margin-bottom: 21px; }

  .brand__mark {
    position: absolute;
    left: 231px;
    top: 63px;
    width: 96px;
    height: 96px;
    border: 2px solid var(--brand-ink);
    border-radius: 50%;
  }
  .brand__ornament {
    position: absolute;
    left: 134px;
    top: 161px;
    width: 290px;
    height: 60px;
    background: radial-gradient(ellipse at 50% 50%, var(--ornament-tone) 0%, var(--ornament-fade) 72%);
  }
  .brand__name {
    position: absolute;
    left: 0; right: 0;
    top: 232px;
    color: var(--brand-ink);
    font-family: "Noticia Text", serif;
    font-weight: 700;
    font-size: 30px;
    line-height: 34px;
    letter-spacing: 1px;
  }
  .brand__tagline {
    position: absolute;
    left: 0; right: 0;
    top: 268px;
    color: var(--brand-ink);
    font-family: "Lato", sans-serif;
    font-weight: 400;
    font-size: 12px;
    line-height: 18px;
    letter-spacing: 4px;
  }
</style>
</head>
<body>
  <section class="card card--front" aria-label="Business card front">
    <div class="contact">
      <p class="contact__name">MARISOL QUENBY</p>
      <p class="contact__role">Director</p>
      <p class="contact__abn">ABN: 31647209853</p>
      <p class="contact__phone">0417906354</p>
      <p class="contact__email">marisolssilvercleaning@tidymail.example</p>
    </div>
  </section>

  <section class="card card--back" aria-label="Business card back">
    <span class="brand__mark" aria-hidden="true"></span>
    <div class="brand__ornament" role="img" aria-label="Symmetrical floral scroll ornament beneath the brand mark"></div>
    <p class="brand__name">SILVER BLOOM</p>
    <p class="brand__tagline">MARISOL’S CLEANING SERVICE</p>
  </section>
</body>
</html>
```